Letterhead, stationery and email signature for construction business

I need the letterhead, stationery and email signature designs for a construction business. I want them to have a corporate feel to them.

I've attached the logo for reference.

```html
<!DOCTYPE html>
<html lang="en">
<head>
<meta charset="utf-8">
<title>Halvern Builds Letterhead</title>
<link href="https://fonts.googleapis.com/css2?family=Lato:wght@400;700&family=Open+Sans:wght@400&family=Italianno&display=swap" rel="stylesheet">
<style>
  :root {
    --brand-blue: #2d56a4;
    --rule-blue: #1f6fc0;
    --slate: #6b6f86;
    --ink: #1a1a1a;
    --contact-ink: #2b2b33;
    --backdrop: #e2e2e2;
    --paper: #ffffff;
  }
  * { margin: 0; padding: 0; box-sizing: border-box; }
  html, body { width: 1200px; height: 1141px; overflow: hidden; background: var(--backdrop); }
  .letterhead {
    position: absolute; left: 210px; top: 20px;
    width: 779px; height: 1101px;
    background: var(--paper);
    box-shadow: 0 4px 14px rgba(0,0,0,.18);
    overflow: hidden;
    font-family: "Lato", sans-serif; color: var(--ink);
  }
  .brand { position: absolute; left: 40px; top: 76px; display: flex; align-items: center; gap: 14px; }
  .brand-mark { width: 46px; height: 46px; background: var(--brand-blue); }
  .brand-name { font-family: "Lato", sans-serif; font-weight: 700; font-size: 38px; color: var(--brand-blue); letter-spacing: .5px; }
  .header-rule { position: absolute; left: 510px; top: 46px; width: 2px; height: 111px; background: var(--rule-blue); }
  .contact { position: absolute; left: 539px; top: 40px; font-family: "Open Sans", sans-serif; font-size: 17px; color: var(--contact-ink); line-height: 22px; font-style: normal; }
  .contact .address { margin-bottom: 8px; }
  .contact-line { display: flex; align-items: center; gap: 6px; }
  .contact-line svg { width: 13px; height: 13px; flex: none; }
  .block { position: absolute; left: 39px; font-size: 16px; line-height: 18.5px; }
  .date { top: 254px; }
  .recipient { top: 292px; }
  .company { top: 346px; }
  .salutation { top: 421px; font-size: 20px; font-weight: 700; }
  .body-copy { top: 464px; width: 701px; font-size: 16px; line-height: 17.3px; text-align: justify; }
  .body-copy p { margin-bottom: 17px; }
  .closing { top: 780px; }
  .signature { top: 876px; font-family: "Italianno", cursive; font-size: 44px; line-height: 1; }
  .footer-band {
    position: absolute; left: 0; bottom: 0; width: 779px; height: 84px;
    background: linear-gradient(180deg, rgba(45,86,164,0) 0%, rgba(45,86,164,.55) 45%, var(--brand-blue) 75%, var(--slate) 100%);
  }
</style>
</head>
<body>
  <main class="letterhead">
    <header>
      <div class="brand">
        <span class="brand-mark"></span>
        <span class="brand-name">Halvern Builds</span>
      </div>
      <div class="header-rule"></div>
      <address class="contact">
        <div class="address">Your address, City<br>State, Zip 1234</div>
        <div class="contact-line">
          <svg viewBox="0 0 16 16"><path fill="#1f6fc0" d="M1 6c0-3 3-4 7-4s7 1 7 4l-3 1-1-2H5L4 7 1 6zm3 2h8l2 5H2l2-5zm4 1a2 2 0 100 4 2 2 0 000-4z"/></svg>
          <span>123 456 789</span>
        </div>
        <div class="contact-line">
          <svg viewBox="0 0 16 16"><rect x="1" y="4" width="14" height="9" fill="#1f6fc0"/><path d="M1 4l7 5 7-5" fill="none" stroke="#fff" stroke-width="1.3"/></svg>
          <span>info@yourgmail.com</span>
        </div>
        <div class="contact-line">
          <svg viewBox="0 0 16 16"><circle cx="8" cy="8" r="7" fill="#1f6fc0"/><path d="M4 5c2 0 2 2 4 2s1 3-1 4M10 3c1 2 3 2 3 4" fill="none" stroke="#fff" stroke-width="1.2"/></svg>
          <span>www.yourwebsite.com</span>
        </div>
      </address>
    </header>

    <div class="block date">January-03-2020</div>
    <div class="block recipient">Mr, James Porter<br>President</div>
    <div class="block company">Northwell Corporation<br>123 Street Name, Suite# 10<br>City, State, 120023</div>
    <div class="block salutation">Dear Mr, James</div>

    <div class="block body-copy">
      <p>Lorem ipsum dolor sit amet, consectetur adipiscing elit, sed do eiusmod tempor incididunt ut labore et dolore magna aliqua. Ut enim ad minim veniam, quis nostrud exercitation ullamco laboris nisi ut aliquip ex ea commodo consequat. Duis aute irure dolor in reprehenderit in voluptate velit esse cillum dolore eu fugiat nulla pariatur.</p>
      <p>Lorem ipsum dolor sit amet, consectetur adipiscing elit, sed do eiusmod tempor incididunt ut labore et dolore magna aliqua. Ut enim ad minim veniam, quis nostrud exercitation ullamco laboris nisi ut aliquip ex ea commodo consequat. Duis aute irure dolor in reprehenderit in voluptate velit esse cillum dolore eu fugiat nulla pariatur.</p>
      <p>Lorem ipsum dolor sit amet, consectetur adipiscing elit, sed do eiusmod tempor incididunt ut labore et dolore magna aliqua. Ut enim ad minim veniam, quis nostrud exercitation ullamco laboris nisi ut aliquip ex ea commodo consequat.</p>
      <p>Excepteur sint occaecat cupidatat non proident, sunt in culpa qui officia deserunt mollit anim id est laborum. re et dolore magnam aliquam quaerat voluptatem.</p>
    </div>

    <div class="block closing">Regards</div>
    <div class="block signature">Daniel Reed</div>

    <div class="footer-band" role="img" aria-label="Decorative blue and grey footer ornament"></div>
  </main>
</body>
</html>
```